Tolbek cards

I want a simple business card that pops.
Logo on one side.
On side two i want.
"Are you thinking about a new building on your property, or renovating an existing structure? Contact".....
Owners Name: Dale Whitacre
Owners Phone number: 610-555-0187
Address:4076 Copper Ridge RD, Ashford Glen, PA 16012
Committed to Quality, Service, and Integrity

```html
<!DOCTYPE html>
<html lang="en">
<head>
<meta charset="utf-8">
<title>Tolbek Builders LLC – Business Cards</title>
<link href="https://fonts.googleapis.com/css2?family=Poppins:wght@400;500;600;800&display=swap" rel="stylesheet">
<style>
  :root {
    --stage: #222222;
    --brown-dark: #432e1e;
    --brown-mid: #5e3d22;
    --tan: #a08a76;
    --pattern-light: #7a5234;
    --white: #ffffff;
    --ink: #2a1e14;
  }
  * { margin: 0; padding: 0; box-sizing: border-box; }
  html, body {
    width: 1200px; height: 800px; overflow: hidden;
    background: var(--stage);
    font-family: "Poppins", sans-serif;
  }
  .canvas { position: relative; width: 1200px; height: 800px; }
  .card {
    position: absolute;
    width: 580px; height: 332px;
    border-radius: 26px;
    overflow: hidden;
    box-shadow: 0 18px 40px rgba(0,0,0,.55);
  }

  /* Back side */
  .card-back { left: 40px; top: 40px; background: var(--brown-dark); }
  .card-back .pattern-fill {
    position: absolute; inset: 0;
    background: radial-gradient(circle at 70% 20%, var(--pattern-light), var(--brown-dark) 75%);
  }
  .card-back .brand {
    position: absolute; inset: 0;
    display: flex; flex-direction: column; align-items: center; justify-content: center;
    color: var(--white); font-weight: 800; text-transform: uppercase;
    line-height: 1;
  }
  .brand-name { font-size: 64px; letter-spacing: 1px; }
  .brand-sub { font-size: 17px; letter-spacing: 2px; margin-top: 6px; }

  /* Front side */
  .card-front { left: 580px; top: 420px; background: var(--white); }
  .card-front .waves { position: absolute; inset: 0; }
  .quote {
    position: absolute; left: 28px; top: 38px; width: 300px;
    font-size: 13.5px; line-height: 1.35; color: var(--ink);
  }
  .card-front .brand {
    position: absolute; right: 36px; top: 30px;
    color: var(--brown-dark); font-weight: 800; text-transform: uppercase;
    line-height: 1; text-align: right;
  }
  .card-front .brand-name { font-size: 52px; }
  .card-front .brand-sub { font-size: 14px; margin-top: 4px; }

  .contact { position: absolute; left: 32px; top: 198px; color: var(--white); }
  .owner-name { font-size: 25px; font-weight: 600; line-height: 1; }
  .owner-role { font-size: 13px; font-weight: 500; line-height: 1.3; margin-top: 2px; }
  .tagline { font-size: 12.5px; line-height: 1.3; margin-top: 6px; margin-left: 12px; }
  .details { list-style: none; margin-top: 8px; margin-left: 24px; font-size: 13px; }
  .details li { display: flex; align-items: center; gap: 10px; height: 19px; }
  .details svg { width: 16px; height: 16px; flex: none; }
</style>
</head>
<body>
<main class="canvas">

  <section class="card card-back" aria-label="Card back">
    <div class="pattern-fill" role="img" aria-label="Repeating brand pattern in brown and gold tones"></div>
    <div class="brand">
      <span class="brand-name">Tolbek</span>
      <span class="brand-sub">Builders LLC</span>
    </div>
  </section>

  <section class="card card-front" aria-label="Card front">
    <svg class="waves" viewBox="0 0 580 332" preserveAspectRatio="none" aria-hidden="true">
      <path d="M0,164 C170,146 330,156 580,118 L580,332 L0,332 Z" fill="var(--tan)"/>
      <path d="M0,170 C180,152 340,164 580,128 L580,332 L0,332 Z" fill="var(--white)"/>
      <path d="M0,176 C180,158 350,170 580,136 L580,332 L0,332 Z" fill="var(--brown-mid)"/>
      <path d="M0,182 C190,166 360,178 580,146 L580,332 L0,332 Z" fill="var(--white)"/>
      <path d="M0,188 C200,172 370,184 580,154 L580,332 L0,332 Z" fill="var(--brown-dark)"/>
    </svg>

    <p class="quote">"Are you thinking about a new building on your property, or renovating an existing structure? Contact" .....</p>

    <div class="brand">
      <div class="brand-name">Tolbek</div>
      <div class="brand-sub">Builders LLC</div>
    </div>

    <div class="contact">
      <h1 class="owner-name">Dale Whitacre</h1>
      <p class="owner-role">Owners</p>
      <p class="tagline">Committed to Quality,<br>Service, and Integrity</p>
      <ul class="details">
        <li>
          <svg viewBox="0 0 16 16"><circle cx="8" cy="8" r="8" fill="var(--white)"/><path d="M5.2 4.2l1.6 0 .6 2-1 .8c.5 1.1 1.3 1.9 2.4 2.4l.8-1 2 .6v1.6c0 .5-.4.8-.9.8C7.5 11.2 4.8 8.5 4.4 5.1c0-.5.3-.9.8-.9z" fill="var(--brown-dark)"/></svg>
          <span>610-555-0187</span>
        </li>
        <li>
          <svg viewBox="0 0 16 16"><circle cx="8" cy="8" r="8" fill="var(--white)"/><path d="M8 3.5a3 3 0 0 0-3 3c0 2.2 3 5.8 3 5.8s3-3.6 3-5.8a3 3 0 0 0-3-3zm0 4.2a1.2 1.2 0 1 1 0-2.4 1.2 1.2 0 0 1 0 2.4z" fill="var(--brown-dark)"/></svg>
          <span>4076 Copper Ridge RD, Ashford Glen, PA 16012</span>
        </li>
      </ul>
    </div>
  </section>

</main>
</body>
</html>
```